Fitness Business Card Design Needed

We are looking for a business card design that stands out but is also simple and unique. I like the idea of on one side using the picture of myself with my logo at my feet. I love the texture on the business card so please take that into account when designing. Then on the other side having my contact details. I want it to be clean, modern, and pretty. I am open to designs that allow spot gloss or gold foiling.

Contact Information for Business Card

Space for Name, Phone number, email, and website

```html
<!DOCTYPE html>
<html lang="en">
<head>
<meta charset="utf-8">
<title>Training Business Card</title>
<link rel="stylesheet" href="https://fonts.googleapis.com/css2?family=Montserrat:wght@300&family=Roboto:wght@300;400&display=swap">
<style>
  :root {
    --backdrop: #8a8a8a;
    --coral: #e8665c;
    --coral-deep: #d9564d;
    --paper: #f4f3f1;
    --gold: #b98a35;
    --ink: #3a3a3a;
    --white: #ffffff;
  }
  * { margin: 0; padding: 0; box-sizing: border-box; }
  html, body { width: 1200px; height: 1200px; overflow: hidden; }
  body { background: var(--backdrop); position: relative; font-family: "Roboto", sans-serif; }

  .card { position: absolute; top: 310px; height: 594px; overflow: hidden; }
  .card--front {
    left: 234px; width: 370px;
    background:
      repeating-linear-gradient(0deg, rgba(0,0,0,0.025) 0 1px, transparent 1px 4px),
      repeating-linear-gradient(90deg, rgba(255,255,255,0.03) 0 1px, transparent 1px 4px),
      var(--coral);
  }
  .card--back {
    left: 648px; width: 364px;
    background:
      repeating-linear-gradient(0deg, rgba(0,0,0,0.02) 0 1px, transparent 1px 4px),
      repeating-linear-gradient(90deg, rgba(0,0,0,0.015) 0 1px, transparent 1px 4px),
      var(--paper);
  }

  .portrait {
    position: absolute; left: 106px; top: 16px; width: 264px; height: 578px;
    border-radius: 120px 120px 0 0;
    background: linear-gradient(180deg, #d9b89a 0%, #c99473 30%, var(--coral-deep) 55%, #c98a6c 80%, #b97d62 100%);
  }

  .brand-vertical {
    position: absolute; left: 0; top: 0; width: 396px; height: 62px;
    transform-origin: 0 0;
    transform: translate(36px, 495px) rotate(-90deg);
    color: var(--white); font-family: "Montserrat", sans-serif; font-weight: 300;
  }
  .brand-vertical__name {
    height: 44px; line-height: 44px; text-align: center; white-space: nowrap;
    font-size: 36px; letter-spacing: 3px;
  }
  .brand-vertical__sub {
    display: flex; align-items: center; gap: 10px; height: 18px; margin-top: 2px;
  }
  .brand-vertical__rule { flex: 1; height: 1.5px; background: var(--white); }
  .brand-vertical__tag { font-size: 14px; letter-spacing: 8px; margin-right: -8px; line-height: 18px; }

  .contact { position: absolute; left: 0; width: 100%; text-align: center; }
  .contact__name { top: 78px; font-size: 23px; color: var(--gold); letter-spacing: 0.5px; }
  .contact__role { top: 104px; font-size: 16px; font-weight: 300; color: var(--ink); letter-spacing: 0.5px; }
  .contact__icons { position: absolute; left: 88px; top: 143px; }
  .contact__lines { top: 176px; font-size: 16px; font-weight: 300; color: var(--ink); line-height: 21.5px; }

  .brand-block {
    position: absolute; left: 52px; top: 498px; width: 260px; text-align: center;
    font-family: "Montserrat", sans-serif; font-weight: 300;
  }
  .brand-block__name { font-size: 24px; letter-spacing: 2px; color: var(--ink); white-space: nowrap; }
  .brand-block__sub { display: flex; align-items: center; gap: 8px; margin-top: 2px; }
  .brand-block__rule { flex: 1; height: 1px; background: var(--gold); }
  .brand-block__tag { font-size: 12px; letter-spacing: 6px; margin-right: -6px; color: var(--gold); }
</style>
</head>
<body>
  <section class="card card--front">
    <div class="portrait" role="img" aria-label="Photo of the trainer standing in a red bikini, hands on hips"></div>
    <div class="brand-vertical">
      <div class="brand-vertical__name">BRIGHTHARBOUR</div>
      <div class="brand-vertical__sub">
        <span class="brand-vertical__rule"></span>
        <span class="brand-vertical__tag">TRAINING</span>
        <span class="brand-vertical__rule"></span>
      </div>
    </div>
  </section>

  <section class="card card--back">
    <div class="contact contact__name">DANIEL HARPER</div>
    <div class="contact contact__role">MANAGING DIRECTOR</div>
    <svg class="contact__icons" width="190" height="26" viewBox="0 0 190 26" aria-hidden="true">
      <line x1="0" y1="13" x2="50" y2="13" stroke="#b98a35" stroke-width="1"/>
      <line x1="140" y1="13" x2="190" y2="13" stroke="#b98a35" stroke-width="1"/>
      <circle cx="69" cy="13" r="12" fill="#b98a35"/>
      <circle cx="95" cy="13" r="12" fill="#b98a35"/>
      <circle cx="121" cy="13" r="12" fill="#b98a35"/>
      <path d="M63 9 h12 v2 h-3 v-1 h-6 v1 h-3 z M65 12 h8 l1 5 h-10 z" fill="#fff"/>
      <rect x="89" y="9" width="12" height="8" fill="#fff"/>
      <path d="M89 9 l6 5 l6 -5" fill="none" stroke="#b98a35" stroke-width="1"/>
      <circle cx="121" cy="13" r="6" fill="none" stroke="#fff" stroke-width="1.5"/>
      <path d="M115 13 h12 M121 7 v12" stroke="#fff" stroke-width="1"/>
    </svg>
    <div class="contact contact__lines">044-987 654 321<br>HELLO@MAILSITE.COM<br>WWW.YOURSITE.COM</div>
    <div class="brand-block">
      <div class="brand-block__name">BRIGHTHARBOUR</div>
      <div class="brand-block__sub">
        <span class="brand-block__rule"></span>
        <span class="brand-block__tag">TRAINING</span>
        <span class="brand-block__rule"></span>
      </div>
    </div>
  </section>
</body>
</html>
```